Upmarket Dessert Lounge needs a Business Card Design

We are an upmarket dessert lounge needing a business card to match our image.

We want something that is simple yet beautiful, feminine, classy, sophisticated and elegant. We want it to stand out and don't mind if it is bold.

The design should include our logo and colours of red or maroon with gold highlights. We don't mind if black is used.

Marlow & Quince

Target Market(s)

For those who like to indulge or treat themselves and give in to their temptations on good quality desserts.

Industry/Entity Type

Business

Requirements
Must have
• Must include our logo and our name

Marlow & Quince

M & Q

```html
<!DOCTYPE html>
<html lang="en">
<head>
<meta charset="utf-8">
<title>Marlow &amp; Quince — Business Card</title>
<link rel="stylesheet" href="https://fonts.googleapis.com/css2?family=Open+Sans:wght@400;600;700&display=swap">
<style>
  :root {
    --backdrop: #d9d9d9;
    --card-black: #000000;
    --maroon: #7a1315;
    --cream: #ffd59a;
    --white: #ffffff;
  }
  * { margin: 0; padding: 0; box-sizing: border-box; }
  html, body {
    width: 956px;
    height: 1200px;
    overflow: hidden;
    background: var(--backdrop);
    font-family: "Open Sans", Arial, sans-serif;
  }
  .canvas { position: relative; width: 956px; height: 1200px; }

  .card {
    position: absolute;
    width: 798px;
    height: 455px;
    background: var(--card-black);
    border-radius: 32px;
    overflow: hidden;
  }
  .card--front { left: 70px; top: 85px; }
  .card--back  { left: 74px; top: 632px; }

  .card__swoosh { position: absolute; inset: 0; width: 100%; height: 100%; }

  .brand-name {
    position: absolute;
    color: var(--cream);
    font-weight: 600;
    white-space: nowrap;
    transform: translate(-50%, -50%);
  }
  .brand-name--monogram { left: 175px; top: 185px; font-size: 64px; letter-spacing: 1px; }
  .brand-name--full { left: 398px; top: 228px; font-size: 40px; letter-spacing: 1px; }

  .identity { position: absolute; left: 401px; top: 72px; color: var(--cream); }
  .identity__name { font-size: 21px; font-weight: 700; line-height: 26px; }
  .identity__role { font-size: 21px; font-weight: 400; line-height: 26px; }

  .contacts {
    position: absolute;
    left: 403px;
    top: 146px;
    list-style: none;
    color: var(--white);
    font-size: 18px;
    line-height: 30px;
  }
  .contacts__label { font-weight: 700; }
  .contacts__item--gap { margin-top: 8px; }

  .address {
    position: absolute;
    left: 72px;
    top: 407px;
    color: var(--white);
    font-size: 18px;
    font-style: normal;
  }
</style>
</head>
<body>
<main class="canvas">

  <section class="card card--front" aria-label="Card front">
    <svg class="card__swoosh" viewBox="0 0 798 455" aria-hidden="true">
      <path d="M740,172 C748,330 650,432 430,455 L618,455 C700,400 752,320 740,172 Z" fill="var(--cream)"/>
      <path d="M636,0 C772,60 792,300 628,455 L798,455 L798,0 Z" fill="var(--maroon)" stroke="var(--card-black)" stroke-width="8"/>
    </svg>

    <div class="brand-name brand-name--monogram">M &amp; Q</div>

    <div class="identity">
      <div class="identity__name">Your Name</div>
      <div class="identity__role">Designation</div>
    </div>

    <ul class="contacts">
      <li><span class="contacts__label">p</span> : 123-456-7890</li>
      <li><span class="contacts__label">c</span> : 123-456-7890</li>
      <li><span class="contacts__label">f</span> : 123-456-7890</li>
      <li class="contacts__item--gap"><span class="contacts__label">e</span> : name@yourwebsite.com</li>
      <li><span class="contacts__label">w</span> : www.marlow&amp;quince.com</li>
    </ul>

    <address class="address">0000, Street Name, City Name, Country Code.</address>
  </section>

  <section class="card card--back" aria-label="Card back">
    <div class="brand-name brand-name--full">MARLOW &amp; QUINCE</div>
  </section>

</main>
</body>
</html>
```